Website redesign www.marigoldlawpc.com law firm site

Need to redesign the website that I currently have to look more modern and professional. Would also like to be able to make updates and post without having a huge hassle. See current www.marigoldlawpc.com. I just think that it looks very immature and it's very templated there's no ability for me to make posts or Add links or anything like that

Target Market(s)

California people looking for a powerhouse attorney in

Industry/Entity Type

Legal

Number of Pages Required

3 page

Font styles to use
Serif
Sans Serif

Colors
ec1f27
000000
ffffff

Requirements
Must have
• Must be mobile friendly. Must look professional and have ability to post links to other websites. Must have ability to post blogs or articles. Would like to be able to read my FeeTrove account and also have the ability to upload forms for people to download
Nice to have
• Simple design easy to use and not cluttered with too much text

```html
<!DOCTYPE html>
<html lang="en">
<head>
<meta charset="utf-8">
<title>Marigold Law, P.C. | Chico California Attorney</title>
<link rel="stylesheet" href="https://fonts.googleapis.com/css2?family=Open+Sans:wght@400;600;700&family=PT+Sans:wght@400;700&family=PT+Serif:ital,wght@0,400;0,700;1,400&display=swap">
<style>
:root{
  --red:#ec1f27;
  --black:#000000;
  --ink:#1a1a1a;
  --grey:#555555;
  --light:#ececec;
  --white:#ffffff;
}
*{box-sizing:border-box;margin:0;padding:0}
html,body{width:1200px;height:3586px;overflow:hidden}
body{font-family:'Open Sans',sans-serif;color:var(--grey);background:var(--white);position:relative}
section,header,footer{position:absolute;left:0;width:1200px}
.abs{position:absolute}

/* header */
.site-header{top:0;height:86px;background:#111}
.brand-name{position:absolute;left:196px;top:0;height:86px;line-height:86px;font-family:'PT Sans',sans-serif;font-weight:700;font-size:22px;color:var(--white);white-space:nowrap}
.main-nav{position:absolute;left:406px;top:0;height:86px;display:flex}
.main-nav a{display:block;height:86px;padding:0 19px;color:var(--white);font-family:'Open Sans',sans-serif;font-weight:700;font-size:12px;line-height:86px;text-decoration:none;text-transform:uppercase}
.main-nav a.active{background:var(--red)}

/* hero */
.hero{top:86px;height:488px;background:linear-gradient(90deg,#3c3c3c 0%,#8a8a8a 30%,#d8d8d8 55%,#a9a9a9 75%,#e6e6e6 100%)}
.hero-promo{left:669px;top:129px;width:323px;height:227px;background:var(--red);padding:22px 22px}
.hero-promo h1{font-family:'PT Sans',sans-serif;font-weight:700;font-size:30px;line-height:36px;color:var(--white);text-transform:uppercase;letter-spacing:.5px}
.hero-promo p{font-size:11px;line-height:17px;color:#fde0e0;margin-top:8px}
.btn-dark{display:inline-block;background:var(--black);color:var(--white);font-family:'Open Sans',sans-serif;font-weight:700;font-size:11px;line-height:14px;padding:10px 22px;margin-top:14px;text-transform:uppercase}
.slider-dots{left:1158px;top:356px}
.slider-dots span{display:block;width:11px;height:11px;border-radius:50%;background:var(--white);margin-bottom:11px}
.slider-dots span.on{background:var(--red)}

/* headings */
.sec-title{position:absolute;left:0;width:1200px;text-align:center;font-family:'PT Sans',sans-serif;font-weight:700;font-size:25px;line-height:32px;color:var(--red);text-transform:uppercase}
.sec-sub{position:absolute;left:0;width:1200px;text-align:center;font-size:11px;line-height:16px;color:#444}
.rule{position:absolute;height:1px;background:#999}

/* intro */
.intro{top:574px;height:449px;background:var(--white)}
.intro .sub-title{position:absolute;left:0;width:1200px;text-align:center;top:82px;font-family:'PT Sans',sans-serif;font-weight:700;font-size:24px;line-height:30px;color:var(--ink);text-transform:uppercase}
.word-cloud{left:220px;top:156px;width:310px;height:215px;background:radial-gradient(ellipse at center,#b41c3d 0%,#d88a96 45%,#fff 75%)}
.intro-text{left:557px;top:186px;width:472px;font-size:11px;line-height:24px;color:#555}

/* about */
.about{top:1023px;height:399px;background:linear-gradient(110deg,#3a3a3a,#262626 50%,#4a4a4a)}
.about-text{left:300px;top:172px;width:600px;text-align:center;font-size:11px;line-height:25px;color:#ddd}

/* practice */
.practice{top:1422px;height:646px;background:var(--white)}
.tile{position:absolute;width:268px;height:191px;background:linear-gradient(135deg,#4a4a4a,#2f2f2f);text-align:center;color:var(--white)}
.tile.featured{background:var(--red)}
.tile .icon{width:44px;height:44px;border-radius:50%;background:var(--red);margin:42px auto 0;display:flex;align-items:center;justify-content:center}
.tile h3{font-family:'PT Sans',sans-serif;font-weight:700;font-size:15px;line-height:20px;text-transform:uppercase;margin-top:10px}
.tile p{font-size:11px;line-height:16px;color:#ddd;margin-top:8px}
.tile.featured h3{margin-top:38px}
.tile.featured p{color:#ffe2e2;line-height:17px;padding:0 38px;margin-top:10px}
.plus{width:22px;height:22px;border:2px solid var(--white);border-radius:50%;margin:10px auto 0;font-family:'Open Sans',sans-serif;font-weight:700;font-size:15px;line-height:17px}

/* blog */
.blog{top:2068px;height:617px;background:var(--light)}
.post-main{left:175px;top:179px;width:482px;height:282px;border:4px solid var(--white);background:linear-gradient(120deg,#c7b6a4,#ece6e0 45%,#6c6f78)}
.post-meta{position:absolute;right:12px;top:10px;font-size:10px;color:#333}
.post-bar{position:absolute;left:0;bottom:0;width:100%;height:56px;background:rgba(0,0,0,.78);padding:10px 14px}
.post-date{font-size:10px;line-height:14px;color:var(--red);font-weight:700;text-transform:uppercase}
.post-title{font-size:11px;line-height:16px;color:var(--white);font-weight:700;margin-top:2px}
.read-more{position:absolute;right:10px;top:10px;background:var(--red);color:var(--white);font-family:'Open Sans',sans-serif;font-weight:700;font-size:11px;line-height:14px;padding:9px 18px;text-transform:uppercase}
.post-excerpt{left:175px;top:481px;width:482px;font-size:11px;line-height:17px;color:#444}
.post-side{width:337px;height:172px;border:4px solid var(--white)}
.post-side .post-bar{height:44px;padding:6px 12px}

/* testimonial */
.testimonial{top:2685px;height:442px;background:var(--red);color:var(--white);text-align:center}
.testimonial h2{position:absolute;top:86px;left:0;width:1200px;font-family:'PT Sans',sans-serif;font-weight:700;font-size:30px;line-height:36px}
.testimonial blockquote{position:absolute;top:140px;left:200px;width:800px;font-family:'PT Serif',serif;font-style:italic;font-size:21px;line-height:34px}
.testimonial cite{position:absolute;top:380px;left:0;width:1200px;font-family:'PT Serif',serif;font-style:italic;font-size:19px;line-height:24px}
.quote-mark{position:absolute;top:292px;left:0;width:1200px;font-family:'PT Serif',serif;font-weight:700;font-size:80px;line-height:80px}
.arrow{position:absolute;top:252px}

/* footer */
.site-footer{top:3127px;height:397px;background:#0d0d0d;color:#bbb}
.foot-brand{position:absolute;left:0;width:1200px;top:58px;text-align:center;color:var(--red);font-family:'PT Sans',sans-serif;font-weight:700;font-size:28px;line-height:34px}
.foot-col{position:absolute;top:138px}
.foot-col h4{font-family:'Open Sans',sans-serif;font-weight:700;font-size:13px;line-height:18px;color:var(--white);margin-bottom:16px}
.foot-col li{list-style:none;font-size:11px;line-height:17px;color:#ccc}
.foot-col p{font-size:11px;line-height:17px;color:#ccc}
.foot-col .map{color:var(--red);font-weight:700}
.badge{position:absolute}
.social{display:flex;gap:16px;margin-top:8px}
.social span{width:14px;height:14px;border-radius:50%;background:#ddd;display:block}
.bottom-bar{position:absolute;top:3524px;left:0;width:1200px;height:62px;background:#000;font-size:10px;line-height:14px;color:#888}
</style>
</head>
<body>

<header class="site-header">
  <div class="brand-name">Marigold Law, P.C.</div>
  <nav class="main-nav">
    <a class="active" href="#">Home</a>
    <a href="#">Attorney Profile</a>
    <a href="#">Practice Areas</a>
    <a href="#">Client Reviews</a>
    <a href="#">Links</a>
    <a href="#">Contact Us</a>
  </nav>
</header>

<section class="hero" role="img" aria-label="Photo of an attorney in a dark suit with arms crossed beside a blurred conference room">
  <div class="hero-promo abs">
    <h1>Marigold Law</h1>
    <p>Lorem ipsum dolor sit amet, consectetur adipiscing elit, sed do eiusmod tempor incididunt ut labore et dolore magna aliqua. Ut enim ad minim veniam, quis nostrud exercitation ullamco.</p>
    <span class="btn-dark">Learn More</span>
  </div>
  <div class="slider-dots abs"><span class="on"></span><span></span><span></span><span></span></div>
</section>

<section class="intro">
  <h2 class="sec-title" style="top:52px">Marigold Law, P.C</h2>
  <div class="rule" style="left:290px;width:150px;top:98px"></div>
  <div class="rule" style="left:760px;width:150px;top:98px"></div>
  <h2 class="sub-title">Chico California Attorney</h2>
  <div class="word-cloud abs" role="img" aria-label="Word cloud illustration featuring the words criminal law, justice and legal"></div>
  <p class="intro-text abs">Find the big firm style legal counsel you can work with in your hometown region at Marigold Law P.C., in Chico, CA. Attorney Dana R. Whitfield, Esq. offers a boutique law firm opportunity for clients who want to enjoy all the advantages of her broad legal experience and education. She works closely with clients, and has the knowledge of many areas of law to apply to your situation. This is very helpful when it is necessary to incorporate those different areas of law practice into creating a winning argument for your unique case.</p>
</section>

<section class="about" role="img" aria-label="Dark photo of law books on a shelf">
  <h2 class="sec-title" style="top:112px">Marigold Law, P.C</h2>
  <div class="rule" style="left:320px;width:140px;top:128px;background:#777"></div>
  <div class="rule" style="left:740px;width:140px;top:128px;background:#777"></div>
  <p class="about-text abs">Marigold Law P.C. is owned by Dana R. Whitfield, a dedicated and caring professional who uses her broad range of skills as a California lawyer to bring consumers and business owners exceptionally strong legal representation that achieves best results. She works with people from across the northern region of California, from the Northern border to the Central Valley region. They bring her legal concerns and problems that occur in many areas of law, including Real Estate, Family law, Business Law, Bankruptcy, Criminal Law and Civil Litigation.</p>
</section>

<section class="practice">
  <h2 class="sec-title" style="top:62px">Practice Areas</h2>
  <div class="rule" style="left:340px;width:150px;top:78px"></div>
  <div class="rule" style="left:710px;width:150px;top:78px"></div>
  <p class="sec-sub" style="top:103px">At Marigold Law, P.C., we offer the following clients services to help you manage all areas of your life that may ever need legal attention:</p>

  <div class="tile featured" style="left:175px;top:158px">
    <h3>Business Law</h3>
    <p>Small and medium-sized businesses have many of the same legal issues that affect large businesses, such as business structure</p>
    <div class="plus">+</div>
  </div>
  <div class="tile" style="left:466px;top:158px" role="img" aria-label="Photo of a house with sale papers">
    <div class="icon"><svg width="18" height="16" viewBox="0 0 18 16"><rect x="1" y="4" width="16" height="11" rx="1" fill="#fff"/><rect x="6" y="1" width="6" height="4" fill="none" stroke="#fff" stroke-width="1.6"/></svg></div>
    <h3>Real Estate Law</h3><p>Small and medium-sized businesses</p>
  </div>
  <div class="tile" style="left:758px;top:158px" role="img" aria-label="Photo of a bankruptcy document">
    <div class="icon"><svg width="18" height="16" viewBox="0 0 18 16"><path d="M9 1 L17 8 H14 V15 H4 V8 H1 Z" fill="#fff"/></svg></div>
    <h3>Bankruptcy</h3><p>Small and medium-sized businesses</p>
  </div>
  <div class="tile" style="left:175px;top:375px" role="img" aria-label="Photo of a family together">
    <div class="icon"><svg width="18" height="16" viewBox="0 0 18 16"><circle cx="6" cy="5" r="3" fill="#fff"/><circle cx="12" cy="5" r="3" fill="#fff"/><rect x="2" y="9" width="14" height="6" rx="3" fill="#fff"/></svg></div>
    <h3>Family Law</h3><p>Small and medium-sized businesses</p>
  </div>
  <div class="tile" style="left:466px;top:375px" role="img" aria-label="Photo of a judge's gavel">
    <div class="icon"><svg width="18" height="16" viewBox="0 0 18 16"><rect x="3" y="2" width="9" height="5" transform="rotate(-35 7 4)" fill="#fff"/><rect x="8" y="7" width="2" height="9" transform="rotate(-35 9 11)" fill="#fff"/></svg></div>
    <h3>Criminal Law</h3><p>Small and medium-sized businesses</p>
  </div>
  <div class="tile" style="left:758px;top:375px" role="img" aria-label="Photo of the scales of justice">
    <div class="icon"><svg width="16" height="16" viewBox="0 0 16 16"><rect x="2" y="1" width="12" height="14" rx="1" fill="#fff"/><rect x="4" y="4" width="8" height="1.5" fill="#ec1f27"/><rect x="4" y="8" width="8" height="1.5" fill="#ec1f27"/></svg></div>
    <h3>Civil Litigation</h3><p>Small and medium-sized businesses</p>
  </div>
</section>

<section class="blog">
  <h2 class="sec-title" style="top:64px">Blog</h2>
  <div class="rule" style="left:400px;width:150px;top:80px"></div>
  <div class="rule" style="left:650px;width:150px;top:80px"></div>
  <p class="sec-sub" style="top:111px">At Marigold Law, P.C., we offer the following clients services to help you manage all areas of your life that may ever need legal attention:</p>

  <article class="post-main abs" role="img" aria-label="Photo of an attorney reviewing documents with a client">
    <div class="post-meta">Comments | Share</div>
    <div class="post-bar">
      <div class="post-date">July 20, 2016</div>
      <div class="post-title">Consectetur adipiscing elit, sed do eiusmod tempor incididunt ...</div>
      <span class="read-more">Read More</span>
    </div>
  </article>
  <p class="post-excerpt abs">Lorem ipsum dolor sit amet, consectetur adipiscing elit, sed do eiusmod tempor incididunt ut labore et dolore magna aliqua. Ut enim ad minim veniam, quis nostrud exercitation ullamco laboris nisi ut aliquip ex ea commodo consequat.</p>

  <article class="post-side abs" style="left:688px;top:179px;background:linear-gradient(120deg,#2e4a3a,#9a7a4a 50%,#c9c4be)" role="img" aria-label="Photo of a statue of justice in front of law books">
    <div class="post-bar"><div class="post-date">July 05, 2016</div><div class="post-title">Adipiscing elit, sed do eiusmod tempor incididunt ...</div></div>
  </article>
  <article class="post-side abs" style="left:688px;top:375px;background:linear-gradient(120deg,#2a2a2a,#8a8a8a 50%,#d6d6d6)" role="img" aria-label="Photo of two business people shaking hands">
    <div class="post-bar"><div class="post-date">July 01, 2016</div><div class="post-title">Adipiscing elit, sed do eiusmod tempor incididunt ...</div></div>
  </article>
</section>

<section class="testimonial">
  <h2>A Vital Component</h2>
  <blockquote>Marigold Law is our go-to source for professional and sound legal advice. Marigold Law has become a vital component to the success of our business as well as the businesses of the clients we have referred to Marigold Law.</blockquote>
  <svg class="arrow" style="left:84px" width="14" height="22" viewBox="0 0 14 22"><path d="M12 2 L3 11 L12 20" fill="none" stroke="#fff" stroke-width="3"/></svg>
  <svg class="arrow" style="left:1102px" width="14" height="22" viewBox="0 0 14 22"><path d="M2 2 L11 11 L2 20" fill="none" stroke="#fff" stroke-width="3"/></svg>
  <div class="quote-mark">&ldquo;</div>
  <div class="rule" style="left:530px;width:140px;top:352px;background:#f47b80"></div>
  <cite>- Ridgeline Accounting Partners</cite>
</section>

<footer class="site-footer">
  <div class="foot-brand">Marigold Law, P.C.</div>
  <div class="foot-col" style="left:175px"><h4>Quick Links</h4><ul><li>Home</li><li>Attorney Profile</li><li>Practice Areas</li><li>Client Reviews</li><li>Links</li><li>Contact Us</li></ul></div>
  <div class="foot-col" style="left:323px"><h4>Other Links</h4><ul><li>Disclaimer</li><li>Site Map</li><li>Sign In</li></ul></div>
  <div class="foot-col" style="left:466px"><h4>Contact Us</h4>
    <p>Call Us (555) 014-2290</p><br>
    <p>Marigold Law, P.C. Office<br>410 Larkspur Avenue | Suite 12<br>Chico, CA 95900</p><br>
    <p>Fax: (555) 014-2291<br>Email: dana@marigoldlawgroup.com</p>
    <p class="map">Map and Directions</p>
  </div>
  <div class="foot-col" style="left:686px"><h4>Rating &amp; Reviews</h4></div>
  <svg class="badge" style="left:706px;top:180px" width="64" height="64" viewBox="0 0 64 64"><circle cx="32" cy="32" r="31" fill="#fff"/></svg>
  <svg class="badge" style="left:792px;top:180px" width="64" height="64" viewBox="0 0 64 64"><circle cx="32" cy="32" r="30" fill="none" stroke="#ccc" stroke-width="2"/></svg>
  <svg class="badge" style="left:866px;top:196px" width="140" height="32" viewBox="0 0 140 32"><rect x="1" y="1" width="138" height="30" fill="none" stroke="#ccc" stroke-width="2"/></svg>
  <div class="foot-col" style="left:686px;top:272px"><h4 style="margin-bottom:6px">Connect With Us</h4><div class="social"><span></span><span></span><span></span></div></div>
</footer>

<div class="bottom-bar">
  <span class="abs" style="left:175px;top:24px">&copy; 2016 Company Name | All Rights Reserved</span>
  <span class="abs" style="left:868px;top:24px">Terms Of Conditions | Privacy Policy</span>
</div>

</body>
</html>
```